Business Card for Coastal Tundrabridge Advisory

We need a business card for Coastal Tundrabridge Advisory. The company website address is provided below. The company logo is attached. We provide specialized permafrost services to the mining, transportation, and oil & gas industries. The card should be prepared for:
Matthias Korhonen, PhD.
Coastal Tundrabridge Advisory
PO Box 418259
Quillwater, Alaska 99642
Direct: +1-907-555-0143
Email: mkorhonen@tundrabridgeadvisory.example
Website: www.coastaltundrabridgeadvisory.example

```html
<!DOCTYPE html>
<html lang="en">
<head>
<meta charset="utf-8">
<title>Coastal Tundrabridge Advisory – Business Card</title>
<link rel="stylesheet" href="https://fonts.googleapis.com/css2?family=Open+Sans:wght@400;600&family=Roboto:wght@400;500;700&display=swap">
<style>
  :root {
    --backdrop: #2b2b2d;
    --card: #0f141f;
    --card-edge: #161c2a;
    --ink: #ffffff;
    --ink-soft: #d9dde6;
    --brand-blue: #22346f;
    --brand-blue-soft: #2a3558;
  }
  * { box-sizing: border-box; margin: 0; padding: 0; }
  html, body {
    width: 1200px; height: 780px; overflow: hidden;
    background: var(--backdrop);
  }
  .stage {
    position: relative; width: 1200px; height: 780px;
    display: flex; align-items: center; justify-content: center; gap: 50px;
  }
  .card {
    position: relative; width: 525px; height: 300px;
    background: var(--card);
    border: 1px solid var(--card-edge);
    box-shadow: 0 18px 40px rgba(0,0,0,.45);
    color: var(--ink);
    font-family: "Roboto", sans-serif;
  }

  /* Front */
  .front .brand {
    position: absolute; top: 34px; left: 34px;
    font-family: "Roboto", sans-serif; font-weight: 500;
    font-size: 19px; letter-spacing: .08em; text-transform: uppercase;
    color: var(--ink); line-height: 1.2; width: 250px;
  }
  .front .holder {
    position: absolute; left: 34px; bottom: 30px;
    font-family: "Open Sans", sans-serif;
  }
  .holder .title { font-size: 14px; font-weight: 400; margin-bottom: 2px; }
  .holder .name { font-size: 27px; line-height: 1.1; }
  .holder .name .first { font-weight: 600; }
  .holder .name .last { font-weight: 400; }

  .contact {
    position: absolute; right: 26px; top: 34px;
    text-align: right; font-size: 12px; line-height: 1.55;
    color: var(--ink-soft); list-style: none;
  }
  .contact li { display: flex; justify-content: flex-end; align-items: center; gap: 7px; }
  .contact .gap { height: 10px; }
  .contact svg { width: 11px; height: 11px; flex: none; }

  /* Back */
  .back .brand-mark {
    position: absolute; left: 0; right: 0; top: 82px;
    text-align: center;
    font-family: "Roboto", sans-serif; font-weight: 500;
    font-size: 30px; letter-spacing: .06em; text-transform: uppercase;
    color: var(--brand-blue); line-height: 1.15; padding: 0 40px;
  }
  .back .services {
    position: absolute; left: 0; right: 0; bottom: 34px;
    text-align: center; padding: 0 24px;
  }
  .services h2 {
    font-size: 12px; font-weight: 700; letter-spacing: .02em;
    text-transform: uppercase; margin-bottom: 4px;
  }
  .services p { font-size: 12.5px; color: var(--ink-soft); }
</style>
</head>
<body>
<main class="stage">
  <section class="card front" aria-label="Business card front">
    <div class="brand">Coastal Tundrabridge Advisory</div>

    <ul class="contact">
      <li>PO Box 418259</li>
      <li>Quillwater, Alaska 99642</li>
      <li class="gap"></li>
      <li>+1-907-555-0143
        <svg viewBox="0 0 12 12" aria-hidden="true"><path d="M3 1.5 L4.6 1.5 L5.4 3.8 L4.3 4.7 Q5.3 6.8 7.3 7.7 L8.2 6.6 L10.5 7.4 L10.5 9 Q10.5 10.5 9 10.5 Q1.5 10 1.5 3 Q1.5 1.5 3 1.5Z" fill="#fff"/></svg>
      </li>
      <li>mkorhonen@tundrabridgeadvisory.example
        <svg viewBox="0 0 12 12" aria-hidden="true"><rect x="1" y="2.5" width="10" height="7" fill="#fff"/><path d="M1 2.5 L6 6.5 L11 2.5" stroke="#0f141f" fill="none"/></svg>
      </li>
      <li>www.coastaltundrabridgeadvisory.example
        <svg viewBox="0 0 12 12" aria-hidden="true"><circle cx="6" cy="6" r="5" fill="#fff"/><path d="M1 6 H11 M6 1 Q3 6 6 11 M6 1 Q9 6 6 11" stroke="#0f141f" stroke-width=".8" fill="none"/></svg>
      </li>
    </ul>

    <div class="holder">
      <div class="title">PhD</div>
      <div class="name"><span class="first">Matthias</span> <span class="last">Korhonen</span></div>
    </div>
  </section>

  <section class="card back" aria-label="Business card back">
    <div class="brand-mark">Coastal Tundrabridge Advisory</div>
    <div class="services">
      <h2>Our Services</h2>
      <p>We provide specialized permafrost services to the mining, transportation, and oil &amp; gas industries</p>
    </div>
  </section>
</main>
</body>
</html>
```